IT Company requires new Business Card design.

Over the years we have had a few different business card designs. We are now due for new cards across the board for all staff. We felt this would be a good time to start fresh with a new design. Our traditional card simply had our details on the front, and a list of services on the back. We don't particularly need the list of services, we have had cards where the only thing on the rear of the card was our logo.
Feel free to be creative, we would like our tag line "Complete IT Management" to appear at some point, doesn't necessarily have to be with the logo.
I have attached samples and drafts of various previous cards we have used over the years.

```html
<!DOCTYPE html>
<html lang="en">
<head>
<meta charset="utf-8">
<title>Cedar Networking – Business Card</title>
<link rel="stylesheet" href="https://fonts.googleapis.com/css2?family=Open+Sans:wght@400;700&display=swap">
<style>
  :root {
    --backdrop: #4a2a1d;
    --card-edge: #2c2c2c;
    --card-base: #333333;
    --card-glow: #4b4b4b;
    --text-main: #ffffff;
    --text-soft: #e6e6e6;
    --mark-grey: #a9a9a9;
  }
  * { box-sizing: border-box; margin: 0; padding: 0; }
  html, body {
    width: 1200px; height: 992px; overflow: hidden;
    background: var(--backdrop);
    font-family: "Open Sans", Arial, sans-serif;
  }
  .canvas { position: relative; width: 1200px; height: 992px; }
  .card {
    position: absolute; top: 44px; width: 548px; height: 881px;
    background: radial-gradient(ellipse 70% 55% at 50% 45%, var(--card-glow), var(--card-base) 70%, var(--card-edge));
    border: 1px solid #262626;
    box-shadow: 0 4px 14px rgba(0,0,0,.45);
    overflow: hidden;
  }
  .card--front { left: 37px; }
  .card--back { left: 637px; }

  .brand-block {
    position: absolute; left: 300px; top: 434px;
    width: 520px;
    transform: translate(-50%, -50%) rotate(-90deg);
    display: flex; flex-direction: column; align-items: center; gap: 28px;
  }
  .brand-row { display: flex; align-items: center; gap: 16px; }
  .brand-square { width: 28px; height: 28px; background: var(--mark-grey); flex: none; }
  .brand-name {
    color: var(--text-main); font-size: 38px; font-weight: 700;
    line-height: 1; white-space: nowrap;
  }
  .tagline {
    color: var(--text-soft); font-size: 22px; font-weight: 400;
    letter-spacing: 7px; text-transform: uppercase; white-space: nowrap;
  }

  .contact { position: absolute; left: 0; right: 0; top: 292px; text-align: center; color: var(--text-main); }
  .person-name { font-size: 27px; font-weight: 700; letter-spacing: .5px; }
  .person-role { font-size: 20px; color: var(--text-soft); margin-top: 4px; text-transform: uppercase; }
  .contact-list { list-style: none; margin-top: 30px; font-size: 20px; color: var(--text-soft); }
  .contact-list li { display: flex; justify-content: center; align-items: center; gap: 8px; height: 36px; }
  .contact-list .gap { width: 14px; }
  .icon { width: 18px; height: 18px; fill: var(--text-soft); flex: none; }
  .address { margin-top: 18px; font-size: 22px; color: var(--text-soft); }
</style>
</head>
<body>
<div class="canvas">
  <section class="card card--front">
    <div class="brand-block">
      <div class="brand-row">
        <div class="brand-square"></div>
        <div class="brand-name">Cedar Networking</div>
      </div>
      <div class="tagline">Complete IT Management</div>
    </div>
  </section>

  <section class="card card--back">
    <div class="contact">
      <div class="person-name">DANIEL HART</div>
      <div class="person-role">Operation Manager</div>
      <ul class="contact-list">
        <li>
          <svg class="icon" viewBox="0 0 24 24"><path d="M6.6 10.8a15 15 0 0 0 6.6 6.6l2.2-2.2c.3-.3.7-.4 1-.2 1.1.4 2.3.6 3.6.6.6 0 1 .4 1 1V20c0 .6-.4 1-1 1A17 17 0 0 1 3 4c0-.6.4-1 1-1h3.5c.6 0 1 .4 1 1 0 1.3.2 2.5.6 3.6.1.3 0 .7-.2 1z"/></svg>
          <span>08 9302 5184</span>
          <span class="gap"></span>
          <svg class="icon" viewBox="0 0 24 24"><path d="M8 1h8a2 2 0 0 1 2 2v18a2 2 0 0 1-2 2H8a2 2 0 0 1-2-2V3a2 2 0 0 1 2-2zm0 3v11h8V4zm1 13v1.5h2V17zm3 0v1.5h2V17zm-3 2.5V21h2v-1.5zm3 0V21h2v-1.5z"/></svg>
          <span>0412 738 906</span>
        </li>
        <li>
          <svg class="icon" viewBox="0 0 24 24"><path d="M7 2h8l3 3v5H7zM4 11h16a2 2 0 0 1 2 2v7a1 1 0 0 1-1 1H3a1 1 0 0 1-1-1v-7a2 2 0 0 1 2-2zm2 4v2h12v-2z"/></svg>
          <span>08 9302 5184</span>
        </li>
        <li>
          <svg class="icon" viewBox="0 0 24 24"><path d="M2 5h20v14H2zm2 2v.5l8 5 8-5V7zm0 3v7h16v-7l-8 5z"/></svg>
          <span>daniel@cedarnetworking.com.au</span>
        </li>
        <li>
          <svg class="icon" viewBox="0 0 24 24"><path d="M12 2a10 10 0 1 0 0 20 10 10 0 0 0 0-20zm6.9 6h-3a15 15 0 0 0-1.3-3.9A8 8 0 0 1 18.9 8zM12 4c.8 1.1 1.5 2.5 1.9 4h-3.8c.4-1.5 1.1-2.9 1.9-4zM4.3 14a8 8 0 0 1 0-4h3.3a16 16 0 0 0 0 4zm.8 2h3a15 15 0 0 0 1.3 3.9A8 8 0 0 1 5.1 16zM8 8H5.1a8 8 0 0 1 4.3-3.9A15 15 0 0 0 8 8zm4 12c-.8-1.1-1.5-2.5-1.9-4h3.8c-.4 1.5-1.1 2.9-1.9 4zm2.3-6H9.7a14 14 0 0 1 0-4h4.6a14 14 0 0 1 0 4zm.3 5.9A15 15 0 0 0 16 16h3a8 8 0 0 1-4.4 3.9zM16.4 14a16 16 0 0 0 0-4h3.3a8 8 0 0 1 0 4z"/></svg>
          <span>www.cedarnetworking.com.au</span>
        </li>
      </ul>
      <div class="address">Unit 7 22 Marlow Street, Bibra Lake WA 6163</div>
    </div>
  </section>
</div>
</body>
</html>
```